Assessment Flyer

We are looking for a marketing flyer for our business. We are a psychology practice that has recently expanded our assessment team and availability. We need a flyer to fax to GP's and other referrers. We have previously sent out rather basic flyers as it was more of a courtesy update about our practice rather than a marketing tool. We have recently created a brochure just focusing on assessments which can be used as a guide for the flyer. We want to update them about our expansion, highlight the assessments we do, introduce our new psychologists, and touch on availability.

```html
<!DOCTYPE html>
<html lang="en">
<head>
<meta charset="utf-8">
<title>Assessment Service Flyer</title>
<link rel="stylesheet" href="https://fonts.googleapis.com/css2?family=Allura&family=Oswald:wght@600&family=Poppins:wght@400;500;600;700&family=Roboto+Slab:wght@700&display=swap">
<style>
  :root {
    --green: #7cc04a;
    --teal: #1f9a80;
    --forest: #0c4236;
    --ink: #13352c;
    --text: #1d2b2a;
    --team-bg: #3f9884;
    --tab: #7dbf4e;
    --portrait: #b58a62;
    --ring: #6cbda8;
    --white: #ffffff;
    --name: #f1fbe8;
  }
  * { box-sizing: border-box; margin: 0; padding: 0; }
  html, body { width: 800px; height: 1200px; overflow: hidden; background: #fff; }
  .flyer { position: relative; width: 800px; height: 1200px; overflow: hidden; font-family: 'Poppins', sans-serif; color: var(--text); }
  .slab { font-family: 'Roboto Slab', serif; font-weight: 700; }

  .hero-photo {
    position: absolute; left: 0; top: 0; width: 800px; height: 720px;
    background:
      radial-gradient(ellipse 420px 260px at 660px 660px, #3f5233 0%, rgba(63,82,51,0.6) 45%, rgba(63,82,51,0) 100%),
      linear-gradient(180deg, #f7f9fb 0%, #e8eef3 22%, #bfcdd9 50%, #8fa3b3 75%, #6a7f8e 100%);
  }

  .brand { position: absolute; left: 58px; top: 44px; display: flex; align-items: center; gap: 12px; }
  .brand-dot { width: 40px; height: 40px; border-radius: 50%; background: var(--green); }
  .brand-name { font-family: 'Roboto Slab', serif; font-weight: 700; font-size: 18px; color: var(--teal); line-height: 1.15; width: 200px; }

  .title { position: absolute; left: 56px; top: 126px; font-size: 50px; line-height: 50px; }
  .title .line-1 { color: var(--green); display: block; }
  .title .line-2 { color: var(--teal); display: block; }
  .title-swoosh { position: absolute; left: 58px; top: 230px; }

  .intro { position: absolute; left: 58px; top: 256px; width: 330px; font-size: 14.5px; line-height: 19px; color: var(--text); }

  .availability { position: absolute; left: 412px; top: 62px; width: 380px; }
  .availability h2 { font-size: 34px; color: var(--ink); line-height: 44px; }
  .short-bar { width: 22px; height: 3px; background: var(--green); margin: 4px 0 8px; }
  .avail-row { display: flex; align-items: center; gap: 8px; }
  .avail-note { font-size: 12px; font-weight: 600; line-height: 14px; color: var(--ink); text-transform: uppercase; white-space: nowrap; }
  .avail-note .accent { color: var(--green); }
  .avail-month { font-family: 'Allura', cursive; font-size: 58px; color: var(--teal); line-height: 1; white-space: nowrap; }
  .avail-year { font-family: 'Oswald', sans-serif; font-weight: 600; font-size: 46px; color: var(--green); line-height: 1; white-space: nowrap; }

  .assess-panel { position: absolute; left: 0; top: 420px; width: 367px; height: 300px; background: var(--forest); border-top-right-radius: 26px; padding: 26px 0 0 58px; }
  .assess-panel h3 { font-size: 31px; line-height: 32px; color: var(--white); }
  .assess-panel h3 span { display: block; color: var(--green); }
  .assess-panel .short-bar { margin: 8px 0 12px; }
  .assess-list { list-style: none; }
  .assess-list li { display: flex; align-items: center; gap: 9px; font-size: 15.5px; line-height: 27px; color: var(--white); }
  .assess-list b { color: var(--green); font-weight: 600; }

  .team { position: absolute; left: 0; top: 720px; width: 800px; height: 480px;
    background: linear-gradient(180deg, #3a8f7c 0%, #3f9884 40%, #46a08b 100%); }
  .team-tab { position: absolute; left: 0; top: 706px; width: 68px; height: 400px; background: var(--tab); border-radius: 0 14px 14px 0; display: flex; align-items: center; justify-content: center; }
  .team-tab span { transform: rotate(-90deg); white-space: nowrap; font-size: 25px; color: var(--forest); }

  .team-grid { position: absolute; left: 80px; top: 750px; width: 700px; display: grid; grid-template-columns: repeat(4, 175px); row-gap: 20px; }
  .member { text-align: center; height: 168px; }
  .portrait { width: 106px; height: 106px; border-radius: 50%; margin: 0 auto 6px; background: radial-gradient(circle at 50% 45%, #c79c73 0%, var(--portrait) 70%); border: 3px solid var(--ring); }
  .member-name { font-size: 15.5px; font-weight: 600; color: var(--name); line-height: 18px; }
  .member-role { font-size: 11px; color: #e3f1ec; line-height: 15px; }

  .call { position: absolute; left: 58px; top: 1128px; display: flex; align-items: center; gap: 8px; }
  .call-label { font-size: 17px; font-weight: 700; color: var(--forest); }
  .call-icon { width: 26px; height: 26px; border-radius: 50%; background: var(--tab); display: flex; align-items: center; justify-content: center; }
  .call-number { font-size: 23px; font-weight: 500; color: var(--white); }
  .web-pill { position: absolute; left: 420px; top: 1120px; width: 380px; height: 40px; background: var(--white); border-radius: 20px 0 0 20px; display: flex; align-items: center; padding-left: 24px; font-size: 15px; font-weight: 600; color: var(--forest); letter-spacing: 0.3px; }
</style>
</head>
<body>
<main class="flyer">
  <div class="hero-photo" role="img" aria-label="Photo of a woman meditating on a grassy mountain ledge above misty blue ranges"></div>

  <div class="brand">
    <span class="brand-dot"></span>
    <span class="brand-name">Riverbend Psychology &amp; Wellness</span>
  </div>

  <h1 class="title slab"><span class="line-1">Assessment</span><span class="line-2">Service</span></h1>
  <svg class="title-swoosh" width="70" height="12" viewBox="0 0 70 12"><path d="M2 9 Q35 1 68 6" fill="none" stroke="#7cc04a" stroke-width="3" stroke-linecap="round"/></svg>

  <p class="intro">Riverbend Psychology and Wellness is excited to announce the expansion of our assessment team. As the need for assessment services has grown, we have worked diligently to expand our team with highly skilled psychologists to support these needs.</p>

  <section class="availability">
    <h2 class="slab">Availability</h2>
    <div class="short-bar"></div>
    <div class="avail-row">
      <p class="avail-note"><span class="accent">Appointments</span><br>Available<br>From early</p>
      <span class="avail-month">March</span>
      <span class="avail-year">2024</span>
    </div>
  </section>

  <section class="assess-panel">
    <h3 class="slab">Available <span>Assessments</span></h3>
    <div class="short-bar"></div>
    <ul class="assess-list">
      <li><svg width="15" height="15" viewBox="0 0 16 16"><circle cx="8" cy="8" r="6.5" fill="none" stroke="#7cc04a" stroke-width="1.6"/><path d="M5 8.2l2.2 2.2L14 3.5" fill="none" stroke="#7cc04a" stroke-width="1.8" stroke-linecap="round"/></svg>Educational Assessment</li>
      <li><svg width="15" height="15" viewBox="0 0 16 16"><circle cx="8" cy="8" r="6.5" fill="none" stroke="#7cc04a" stroke-width="1.6"/><path d="M5 8.2l2.2 2.2L14 3.5" fill="none" stroke="#7cc04a" stroke-width="1.8" stroke-linecap="round"/></svg><span><b>ADHD:</b> Children and Adults</span></li>
      <li><svg width="15" height="15" viewBox="0 0 16 16"><circle cx="8" cy="8" r="6.5" fill="none" stroke="#7cc04a" stroke-width="1.6"/><path d="M5 8.2l2.2 2.2L14 3.5" fill="none" stroke="#7cc04a" stroke-width="1.8" stroke-linecap="round"/></svg><span><b>Autism:</b> Children and Adults</span></li>
      <li><svg width="15" height="15" viewBox="0 0 16 16"><circle cx="8" cy="8" r="6.5" fill="none" stroke="#7cc04a" stroke-width="1.6"/><path d="M5 8.2l2.2 2.2L14 3.5" fill="none" stroke="#7cc04a" stroke-width="1.8" stroke-linecap="round"/></svg>Intellectual Disability</li>
      <li><svg width="15" height="15" viewBox="0 0 16 16"><circle cx="8" cy="8" r="6.5" fill="none" stroke="#7cc04a" stroke-width="1.6"/><path d="M5 8.2l2.2 2.2L14 3.5" fill="none" stroke="#7cc04a" stroke-width="1.8" stroke-linecap="round"/></svg>Giftedness</li>
    </ul>
  </section>

  <section class="team" role="img" aria-label="Soft teal forest backdrop for the team section"></section>
  <div class="team-tab"><span class="slab">Meet the assessment team</span></div>

  <div class="team-grid">
    <div class="member"><div class="portrait" role="img" aria-label="Portrait of Karen Holloway"></div><p class="member-name">Karen Holloway</p><p class="member-role">Clinical Director</p></div>
    <div class="member"><div class="portrait" role="img" aria-label="Portrait of Dr Megan Whitfield"></div><p class="member-name">Dr Megan Whitfield</p><p class="member-role">Registered Psychologist</p></div>
    <div class="member"><div class="portrait" role="img" aria-label="Portrait of Dr Helen Marsh"></div><p class="member-name">Dr Helen Marsh</p><p class="member-role">Counselling Psychologist</p></div>
    <div class="member"><div class="portrait" role="img" aria-label="Portrait of Nadia Ferraro"></div><p class="member-name">Nadia Ferraro</p><p class="member-role">Registered Psychologist</p></div>
    <div class="member"><div class="portrait" role="img" aria-label="Portrait of Chiara Bellini"></div><p class="member-name">Chiara Bellini</p><p class="member-role">Registered Psychologist</p></div>
    <div class="member"><div class="portrait" role="img" aria-label="Portrait of Valeria Ortiz Kendall"></div><p class="member-name">Valeria Ortiz<br>Kendall</p><p class="member-role">Registered Psychologist</p></div>
    <div class="member"><div class="portrait" role="img" aria-label="Portrait of Emily Dawson"></div><p class="member-name">Emily Dawson</p><p class="member-role">Provisional Psychologist</p></div>
    <div class="member"><div class="portrait" role="img" aria-label="Portrait of Grace Holden"></div><p class="member-name">Grace Holden</p><p class="member-role">Provisional Psychologist</p></div>
  </div>

  <div class="call">
    <span class="call-label">Call us now at!</span>
    <span class="call-icon"><svg width="14" height="14" viewBox="0 0 24 24"><path d="M6.6 10.8a15.1 15.1 0 0 0 6.6 6.6l2.2-2.2c.3-.3.7-.4 1-.2 1.1.4 2.3.6 3.6.6.6 0 1 .4 1 1V20c0 .6-.4 1-1 1A17 17 0 0 1 3 4c0-.6.4-1 1-1h3.5c.6 0 1 .4 1 1 0 1.3.2 2.5.6 3.6.1.3 0 .7-.2 1z" fill="#ffffff"/></svg></span>
    <span class="call-number">(08) 7120 4385</span>
  </div>
  <div class="web-pill">www.riverbendpsychology.com.au</div>
</main>
</body>
</html>
```